Tradlo - Forex Signal Services Moments Matter Most. Reshape your path.

I need an attractive eye catching web design that is azure friendly. I currently have a web programmer working on the backend of my website. Now I need a professional design to attract and retain customers. This site needs to be mobile friendly.

Tradlo is a highly reputable, trustworthy and professional site that offers forex signals to traders in all parts of the globe. With accurate and reliable forex signals, traders can not only make money but also boost their profits.

At Tradlo, we want our clients to have complete faith on us and our services! We also do not want our users to lead a simple and monotonous life. Instead our goal is to help them create an extra source of steady income. However, this is possible only when our clients resolve to change their lives for the better. They need to change their mindset and most importantly develop a positive frame of mind. That’s exactly why at Tradlo, we provide our clients with innumerable personal development tools and resources that’ll aid them in changing all the aspects of their lives. We want our traders to feel inspired and educate them in the right way!

Colors are flexible.

I do like the simplicity of www.brightmarkvo.example.
I do want a design more professional in appearance and not everything on page one.

I have not been able to decide on a logo. There is one of lower quality as I have not paid for it yet but I will if you decide it's the best for my business I will. Or should one feel that they have a better idea for a logo, I will pay for it if i like it.

I have included some of the content of my site so you can get a feel for where I am coming from.
(Please note that this content is still in the editing process)
Updates

Project Deadline Extended Reason: My content was not complete nor finalization of the final logo. We will allow a few more days for designers to modify the website.Thank you for your patience and understanding. Added Tuesday, January 24, 2017

Target Market(s)

I work with Forex Traders, Investors wanting to control their own portfolios, and remote nomads/mellienials

Coding

Coded - Design and coding required

Number of Pages Required

5+ page

Requirements
Must have
• I must have a professional clean look. I want the site to be interactive and eye catching. I want my audience hooked within seconds of opening it. It has to have all important information first. Photos must be legit and not spammy. I work as a representative in the financial market. I want my site to reflect that I stand by my product and reputation means everything to me. This site has to be engaging.
• Sorry, I should have included this earlier of what I will all need on this site.
• I'll have about Tradlo (my company, what we stand for, who we work with, my strategy, etc....
• about me (why i started this company, who I am)
• Performance (graphs and recent posts of signals)
• Membership (how to sign up)
• Terms of service/legal/disclaimers
• FAQS
• Personal Development Resources
• Forex Education Resources
Nice to have
• Quick links to bounce around the site faster.
Should not have
• I do not want over the top white collar conservative.

```html
<!DOCTYPE html>
<html lang="en">
<head>
<meta charset="utf-8">
<title>Tradlo – Forex Signal Services</title>
<link rel="stylesheet" href="https://fonts.googleapis.com/css2?family=Nunito:wght@400;600;700;800;900&family=Nunito+Sans:wght@400;600;700&display=swap">
<style>
:root{
  --gold:#fdb813;
  --gold-dark:#e9a500;
  --ink:#1e1e1e;
  --night:#111418;
  --charcoal:#262626;
  --grey-text:#555;
  --light:#f2f2f2;
  --white:#fff;
}
*{box-sizing:border-box;margin:0;padding:0}
html,body{width:1200px;height:3543px;overflow:hidden}
body{font-family:"Nunito Sans",Arial,sans-serif;color:var(--ink);background:var(--white);font-size:12px;line-height:1.5}
.page{position:relative;width:1200px;height:3543px}
section,header,footer{position:absolute;left:0;width:1200px}
.photo{position:absolute}
.heading-deco{display:block;width:46px;height:14px;border-top:3px solid currentColor;border-left:3px solid currentColor;margin-bottom:8px}
.section-title{font-family:"Nunito",sans-serif;font-weight:900;font-size:38px;line-height:1;letter-spacing:.5px}
.section-sub{font-family:"Nunito",sans-serif;font-weight:800;font-size:9px;letter-spacing:.5px;text-transform:uppercase;margin-top:4px}
.btn{display:inline-block;font-family:"Nunito",sans-serif;font-weight:800;font-size:11px;text-transform:uppercase;padding:0 30px;height:26px;line-height:26px}
.btn-dark{background:var(--charcoal);color:var(--white)}
.btn-gold{background:var(--gold);color:var(--ink)}

/* Header */
.topbar{top:0;height:20px;background:var(--gold);font-size:8.5px;font-weight:700}
.topbar-info{position:absolute;left:388px;top:4px;display:flex;gap:40px}
.topbar-info b{font-weight:800}
.currency{position:absolute;left:872px;top:0;height:20px;width:50px;background:var(--ink);color:var(--white);text-align:center;line-height:20px;font-size:9px}
.cart{position:absolute;left:930px;top:4px}
.hero{top:0;height:540px;overflow:hidden}
.hero-bg{left:0;top:20px;width:1200px;height:520px;background:radial-gradient(ellipse at 30% 40%,#3a1d12 0%,#1a1512 35%,#0c1410 70%,#08100d 100%)}
.navbar{top:20px;height:50px;background:rgba(10,10,10,.55)}
.logo-box{position:absolute;left:248px;top:0;width:125px;height:118px;background:var(--white);clip-path:polygon(0 0,100% 0,100% 78%,50% 100%,0 78%);z-index:3;display:flex;flex-direction:column;align-items:center;justify-content:center}
.logo-mark{width:22px;height:22px;border-radius:50%;background:var(--gold);margin-bottom:6px}
.logo-name{font-family:"Nunito",sans-serif;font-weight:800;font-size:22px;color:var(--ink);line-height:1}
.nav{position:absolute;left:425px;top:37px;display:flex;gap:16px;font-family:"Nunito",sans-serif;font-weight:700;font-size:10.5px;color:var(--white);text-transform:uppercase;z-index:2}
.nav .active{border-bottom:2px solid var(--gold);padding-bottom:12px}
.hero-content{position:absolute;left:0;top:170px;width:1200px;text-align:center;color:var(--white)}
.hero-kicker{font-family:"Nunito",sans-serif;font-weight:900;font-size:58px;color:var(--gold);line-height:1}
.hero-title{font-family:"Nunito",sans-serif;font-weight:600;font-size:40px;line-height:1.15;text-transform:uppercase}
.hero-lead{width:560px;margin:12px auto 0;font-size:10px;line-height:1.45}
.hero-lead b{color:var(--gold)}
.hero-offer{font-family:"Nunito",sans-serif;font-weight:800;font-size:28px;margin-top:10px}
.search{display:flex;width:454px;height:36px;margin:14px auto 0;background:var(--white)}
.search span{flex:1;text-align:left;padding:9px 12px;font-size:11px;color:var(--ink)}
.search i{width:36px;background:var(--gold);display:flex;align-items:center;justify-content:center}

/* About */
.about{top:540px;height:617px;background:var(--white)}
.about-text{position:absolute;left:253px;top:58px;width:430px;color:var(--gold)}
.about-text .section-sub{color:var(--ink)}
.about-copy{color:var(--grey-text);font-size:10px;margin-top:30px;line-height:1.55}
.about-copy p+p{margin-top:10px}
.features{position:absolute;left:253px;top:270px;display:grid;grid-template-columns:212px 212px;row-gap:26px}
.feature-icon{width:50px;height:50px;border-top:3px solid var(--gold);border-left:3px solid var(--gold);display:flex;align-items:center;justify-content:center;margin-bottom:22px}
.feature h3{font-family:"Nunito",sans-serif;font-weight:900;font-size:14px;letter-spacing:.3px}
.feature p{font-size:8.5px;color:var(--grey-text);width:165px;line-height:1.4}
.about-photo{left:640px;top:40px;width:494px;height:577px;background:radial-gradient(ellipse at 55% 45%,#cfd6de 0%,#aab7c6 45%,#e9ecef 80%,#fff 100%)}

/* Strategy */
.strategy{top:1157px;height:454px}
.strategy-panel{position:absolute;left:0;top:0;width:626px;height:454px;background:var(--gold)}
.strategy-photo{left:626px;top:0;width:574px;height:454px;background:linear-gradient(135deg,#0b2230 0%,#0f3140 40%,#07161f 100%)}
.strategy-text{position:absolute;left:253px;top:54px;width:360px;color:var(--white)}
.strategy-text .section-sub{color:var(--white)}
.strategy-copy{font-size:10px;color:var(--ink);margin-top:26px;line-height:1.55}
.strategy-copy p+p{margin-top:12px}
.strategy-text .btn{margin-top:28px}

/* Forex traders */
.traders{top:1611px;height:279px;background:radial-gradient(ellipse at 50% 50%,#2a3a4a 0%,#141d28 55%,#0a1018 100%);text-align:center;color:var(--white)}
.centered-head{display:flex;flex-direction:column;align-items:center}
.centered-head .heading-deco{align-self:center;margin-left:46px}
.traders .centered-head{margin-top:50px}
.traders .section-title{font-size:32px}
.traders .section-sub{color:var(--gold)}
.traders p{width:640px;margin:16px auto 0;font-size:11.5px;line-height:1.4}
.traders .btn{margin-top:14px;font-size:10px;padding:0 26px}

/* Membership */
.membership{top:1890px;height:500px;background:var(--white);text-align:center}
.membership .centered-head{margin-top:60px;color:var(--gold)}
.membership .section-title{font-size:34px}
.membership .section-sub{color:var(--ink)}
.plans{position:absolute;left:274px;top:177px;display:flex;gap:23px}
.plan{width:201px;height:271px;background:var(--light)}
.plan-price{height:79px;background:var(--white);display:flex;justify-content:center;align-items:flex-start;padding-top:0}
.price-frame{width:52px;height:54px;border:3px solid var(--ink);border-bottom:none;margin-top:0;display:flex;flex-direction:column;justify-content:center;font-family:"Nunito",sans-serif;line-height:1}
.price-frame b{font-size:14px;font-weight:800}
.price-frame small{font-size:7px;font-weight:700}
.plan-term{height:25px;background:var(--gold);font-family:"Nunito",sans-serif;font-weight:900;font-size:13px;line-height:25px}
.plan ul{list-style:none;margin-top:14px}
.plan li{font-size:8.5px;height:21px;line-height:21px;color:var(--ink)}
.plan li:nth-child(even){background:var(--white)}
.plan .btn{margin-top:14px;height:18px;line-height:18px;font-size:9px;padding:0 16px;text-transform:none}

/* Why us */
.why{top:2390px;height:456px;background:var(--gold)}
.why-photo{left:0;top:0;width:508px;height:456px;background:linear-gradient(135deg,#0e4d7a 0%,#1e75ad 40%,#0a3a60 100%)}
.why-text{position:absolute;left:543px;top:48px;width:410px;color:var(--white)}
.why-text .section-sub{color:var(--ink)}
.why-copy{font-size:9.5px;color:var(--ink);margin-top:26px;line-height:1.5}
.why-list{list-style:none;margin-top:12px;padding-left:20px}
.why-list li{font-size:9px;color:var(--ink);margin-bottom:5px;position:relative}
.why-list li::before{content:"";position:absolute;left:-12px;top:6px;width:4px;height:4px;border-radius:50%;background:var(--ink)}
.why-text .btn{margin-top:14px}

/* Investors */
.investors{top:2846px;height:260px;background:radial-gradient(ellipse at 50% 40%,#2a2a2a 0%,#141414 60%,#0a0a0a 100%);color:var(--white);text-align:center}
.investors .centered-head{margin-top:50px}
.investors .section-title{font-size:32px}
.investors .section-sub{color:var(--gold)}
.investors p{width:640px;margin:16px auto 0;font-size:11.5px;line-height:1.45}

/* Newsletter */
.newsletter{top:3106px;height:149px;background:var(--gold)}
.newsletter-head{position:absolute;left:253px;top:52px}
.newsletter-head .heading-deco{color:var(--ink);width:40px;height:10px}
.newsletter-head small{display:block;font-family:"Nunito",sans-serif;font-weight:900;font-size:10px}
.newsletter-head strong{display:block;font-family:"Nunito",sans-serif;font-weight:900;font-size:16px;line-height:1}
.newsletter-field{position:absolute;left:543px;top:80px;width:402px;border-bottom:1px solid var(--ink);display:flex;justify-content:space-between;font-size:9px;padding-bottom:3px}

/* Footer */
.footer{top:3255px;height:288px;background:var(--ink);color:var(--white)}
.footer-cols{position:absolute;left:253px;top:42px;display:grid;grid-template-columns:184px 205px 180px 200px}
.footer h4{font-family:"Nunito",sans-serif;font-weight:900;font-size:17px;color:var(--gold);margin-bottom:14px;letter-spacing:.3px}
.footer p{font-size:8.5px;line-height:1.45;width:160px}
.footer .gains p{margin-bottom:10px}
.footer-links{list-style:none}
.footer-links li{font-size:9px;margin-bottom:14px;display:flex;align-items:center;gap:8px}
.contact li{font-size:9px;margin-bottom:10px;display:flex;gap:8px;align-items:flex-start;list-style:none}
.socials{display:flex;gap:8px;margin-top:6px}
.socials span{width:22px;height:22px;border:1.5px solid var(--gold);border-radius:50%}
.copyright{position:absolute;left:0;bottom:0;width:1200px;height:24px;background:var(--gold);color:var(--ink);font-size:8px;font-weight:700}
.copyright span{position:absolute;left:253px;top:6px}
</style>
</head>
<body>
<div class="page">

<header class="hero">
  <div class="photo hero-bg" role="img" aria-label="Dark forex market backdrop with glowing price tables and chart lines"></div>
  <div class="topbar" style="position:absolute;left:0;width:1200px">
    <div class="topbar-info">
      <span><b>Phone Number :</b> 000 000 000</span>
      <span><b>Email :</b> info@tradlo.example</span>
      <span><b>Address :</b> My Best Lesson ABC, Street Your City</span>
    </div>
    <div class="currency">USD ▾</div>
    <svg class="cart" width="13" height="12" viewBox="0 0 13 12"><path d="M0 1h2l2 7h7l2-5H3.5" fill="none" stroke="#1e1e1e" stroke-width="1.6"/><circle cx="5" cy="10.5" r="1.2" fill="#1e1e1e"/><circle cx="10" cy="10.5" r="1.2" fill="#1e1e1e"/></svg>
  </div>
  <div class="navbar" style="position:absolute;left:0;width:1200px"></div>
  <div class="logo-box"><span class="logo-mark"></span><span class="logo-name">Tradlo</span></div>
  <nav class="nav">
    <span class="active">Home</span><span>Welcome</span><span>Membership Plans</span><span>Performance</span><span>FAQ</span><span>Contact</span><span>Free Trial</span><span>Forex Resources</span>
  </nav>
  <div class="hero-content">
    <div class="hero-kicker">WELCOME TO</div>
    <div class="hero-title">Tradlo Reshape Your Path</div>
    <p class="hero-lead"><b>FOREX SIGNAL SERVICES MOMENTS MATTER MOST. RESHAPE YOUR PATH.</b> We use proven strategies to help traders in succeeding in the forex market. Our forex experts provide high-probability, professional and consistent forex signals and charts that help traders in maximizing their profits and eliminating losses.</p>
    <div class="hero-offer">New .COMs only $11.99!*</div>
    <div class="search"><span>Search</span><i><svg width="14" height="14" viewBox="0 0 14 14"><circle cx="6" cy="6" r="4.5" fill="none" stroke="#1e1e1e" stroke-width="2"/><path d="M9.5 9.5 13 13" stroke="#1e1e1e" stroke-width="2"/></svg></i></div>
  </div>
</header>

<section class="about">
  <div class="about-text">
    <span class="heading-deco"></span>
    <h2 class="section-title">ABOUT ME</h2>
    <div class="section-sub">About the owner/about the founder</div>
    <div class="about-copy">
      <p>Pardon my language but there is a lot of 'crap', on the internet, especially when it comes to the services I offer. I have spent countless hours and years of my life towards my passion for the currency industry. I finally developed a strategy I am proud of and stand by my product with my name and company brand.</p>
      <p>I believe life was meant to be experienced.<br>My life mission is to grow, teach and apply what I've learnt to my future.</p>
    </div>
  </div>
  <div class="features">
    <div class="feature">
      <div class="feature-icon"><svg width="22" height="22" viewBox="0 0 22 22"><circle cx="11" cy="11" r="8" fill="none" stroke="#fdb813" stroke-width="2" stroke-dasharray="4 3"/><circle cx="11" cy="11" r="3" fill="#fdb813"/></svg></div>
      <h3>STRATEGY</h3>
      <p>I am a college graduate specializing in Business Administration, worked in the finance background for years</p>
    </div>
    <div class="feature">
      <div class="feature-icon"><svg width="22" height="22" viewBox="0 0 22 22"><path d="M3 3h7v3a2 2 0 1 0 3 0V3h6v7h-3a2 2 0 1 0 0 3h3v6H3z" fill="#fdb813"/></svg></div>
      <h3>PUZZLE.</h3>
      <p>I am a college graduate specializing in Business Administration, worked in the finance background for years</p>
    </div>
    <div class="feature">
      <div class="feature-icon"><svg width="22" height="22" viewBox="0 0 22 22"><path d="M3 10h4v10H3zM8 10l4-7c2 0 2 2 1.5 4H19c1 0 1.5 1 1.2 2l-2 9c-.2.6-.7 1-1.3 1H8z" fill="#fdb813"/></svg></div>
      <h3>DEDICATION</h3>
      <p>I am a college graduate specializing in Business Administration, worked in the finance background for years</p>
    </div>
    <div class="feature">
      <div class="feature-icon"><svg width="22" height="22" viewBox="0 0 22 22"><circle cx="11" cy="11" r="9" fill="none" stroke="#fdb813" stroke-width="2"/><circle cx="11" cy="11" r="5" fill="none" stroke="#fdb813" stroke-width="2"/><circle cx="11" cy="11" r="1.8" fill="#fdb813"/></svg></div>
      <h3>PRECISION</h3>
      <p>I am a college graduate specializing in Business Administration, worked in the finance background for years</p>
    </div>
  </div>
  <div class="photo about-photo" role="img" aria-label="Portrait of the founder in a light blue shirt, arms crossed"></div>
</section>

<section class="strategy">
  <div class="strategy-panel"></div>
  <div class="photo strategy-photo" role="img" aria-label="Close-up of a trading screen showing green price quotes and charts"></div>
  <div class="strategy-text">
    <span class="heading-deco"></span>
    <h2 class="section-title">OUR STRATEGY</h2>
    <div class="section-sub">About the owner/about the founder</div>
    <div class="strategy-copy">
      <p>Tradlo.com works with both day as well as intraday traders. We only hold a maximum of one position at any given point in time. Once we've placed an order we do not move SL or TP targets.</p>
      <p>We follow naked forex trading techniques including price action, immediate trend and personalized mathematical formulas. Our success stems from our strict enforcement of discipline, patience, attitude, economics and timing to help our traders maximize their gains from forex trading. (please edit). At Tradlo, we trade GBRUSD, EURUSD, AUDUSD, USDCHF and USDJPY pairs only and target anywhere between 25-50 pips a day with a risk/reward ratio of at least 2:1.</p>
      <p>Our maximum drawdown is 18% and we strive to average 150-250 pips per month. We strongly recommend no more than 3% leveraged risk of your account for any trade. Most trades are closed within hours. Click here to learn more about Forex Basics!</p>
    </div>
    <span class="btn btn-dark">Read More</span>
  </div>
</section>

<section class="traders">
  <div class="photo" style="inset:0" role="img" aria-label="Dim world map of trading hubs behind the heading"></div>
  <div class="centered-head" style="position:relative">
    <span class="heading-deco" style="color:var(--gold)"></span>
    <h2 class="section-title">FOREX TRADERS</h2>
    <div class="section-sub">About the owner/about the founder</div>
  </div>
  <p style="position:relative">A Forex signal service is provided for those who are struggling to make money on the forex market. We know that the forex market is ruthless and can cut you in so many ways if you are not well versed with it. Some forex traders may deny this but I have been in this market long enough to know that this is true.</p>
  <span class="btn btn-gold" style="position:relative">Read More</span>
</section>

<section class="membership">
  <div class="centered-head">
    <span class="heading-deco"></span>
    <h2 class="section-title">MEMBERSHIP PLANS</h2>
    <div class="section-sub">About the owner/about the founder</div>
  </div>
  <div class="plans">
    <div class="plan">
      <div class="plan-price"><div class="price-frame"><b>$59</b><small>USD</small></div></div>
      <div class="plan-term">1 MONTH</div>
      <ul><li>Click here to sign up for 1 month</li><li>Click here to sign up for 1 month</li><li>Click here to sign up for 1 month</li><li>Click here to sign up for 1 month</li></ul>
      <span class="btn btn-dark">Order Now</span>
    </div>
    <div class="plan">
      <div class="plan-price"><div class="price-frame"><b>$149</b><small>USD</small></div></div>
      <div class="plan-term">3 MONTH</div>
      <ul><li>Click here to sign up for 3 month</li><li>Click here to sign up for 3 month</li><li>Click here to sign up for 3 month</li><li>Click here to sign up for 3 month</li></ul>
      <span class="btn btn-dark">Order Now</span>
    </div>
    <div class="plan">
      <div class="plan-price"><div class="price-frame"><b>$549</b><small>USD</small></div></div>
      <div class="plan-term">12 MONTH</div>
      <ul><li>Click here to sign up for 12 month</li><li>Click here to sign up for 12 month</li><li>Click here to sign up for 12 month</li><li>Click here to sign up for 12 month</li></ul>
      <span class="btn btn-dark">Order Now</span>
    </div>
  </div>
</section>

<section class="why">
  <div class="photo why-photo" role="img" aria-label="Blue trading screen with price figures and rising chart lines"></div>
  <div class="why-text">
    <span class="heading-deco"></span>
    <h2 class="section-title">WHY US</h2>
    <div class="section-sub">About the owner/about the founder</div>
    <p class="why-copy">Put simply, because we're different! We are a 'Never before Seen' forex trading company that is focused on guiding, mentoring and assisting traders in every possible manner! We provide tools, resources and technology that allow traders to fulfill their trading aspirations and achieve success.</p>
    <ul class="why-list">
      <li>We offer speedy, convenient, accurate and desired results.</li>
      <li>We're a highly dependable and trusted forex trading platform.</li>
      <li>Our motto is to 'Reshape Your Path' and also to ensure that you earn profits on a regular basis.</li>
      <li>Our objective is to provide global access to trusted forex signals.</li>
      <li>Our services are highly affordable.</li>
      <li>We offer High Probable forex strategies with high rewards.</li>
      <li>We set transparent entry price and exit levels.</li>
      <li>Our team will constantly update you regarding the status of your trade till the time it is closed.</li>
    </ul>
    <span class="btn btn-dark">Read More</span>
  </div>
</section>

<section class="investors">
  <div class="centered-head">
    <span class="heading-deco" style="color:var(--gold)"></span>
    <h2 class="section-title">INVESTORS</h2>
    <div class="section-sub">About the owner/about the founder</div>
  </div>
  <p>I will show you how you can invest your money and manage it yourself.<br>No need to hire someone else to look after your investment for you and you don't even need to know how to trade forex to benefit from my services. Everything you need to get started is made available to you here.</p>
</section>

<section class="newsletter">
  <div class="newsletter-head">
    <span class="heading-deco"></span>
    <small>NEWSLETTER FOR RECEIVE</small>
    <strong>OUR LATEST COMPANY UPDATES</strong>
  </div>
  <div class="newsletter-field"><span>Your Email</span><svg width="10" height="10" viewBox="0 0 10 10"><path d="M0 5 10 0 7 10 5 6z" fill="#1e1e1e"/></svg></div>
</section>

<footer class="footer">
  <div class="footer-cols">
    <div>
      <h4>ABOUT US</h4>
      <p>Pardon my language but there is a lot of 'crap', on the internet, especially when it comes to the services I offer. I have spent countless hours and years of my life towards my passion for the currency industry. I finally developed a strategy I am proud of and stand by my product with my name and company brand.</p>
    </div>
    <div class="gains">
      <h4>YOU MAKE MONEY</h4>
      <p>150-250+ pips per month!</p>
      <p>A maximum of 15 to 30 signals is sent per month.</p>
      <p>Expect to make 30-50 pips per signal</p>
    </div>
    <div>
      <h4>COMPANY LINKS</h4>
      <ul class="footer-links">
        <li>› Our History</li><li>› Mission &amp; Vision</li><li>› Careers</li><li>› Partners</li><li>› Our Team</li><li>› Testimonials</li>
      </ul>
    </div>
    <div>
      <h4>HEAD OFFICE</h4>
      <ul class="contact">
        <li><svg width="9" height="11" viewBox="0 0 9 11"><path d="M4.5 0a4 4 0 0 1 4 4c0 3-4 7-4 7S.5 7 .5 4a4 4 0 0 1 4-4z" fill="#fff"/><circle cx="4.5" cy="4" r="1.5" fill="#1e1e1e"/></svg><span>My Best Lesson ABC, Street<br>Your City</span></li>
        <li><svg width="10" height="8" viewBox="0 0 10 8"><rect width="10" height="8" fill="#fff"/><path d="M0 0 5 4 10 0" fill="none" stroke="#1e1e1e"/></svg><span>admin@tradlo.example</span></li>
        <li><svg width="10" height="8" viewBox="0 0 10 8"><rect width="10" height="8" fill="#fff"/><path d="M0 0 5 4 10 0" fill="none" stroke="#1e1e1e"/></svg><span>support@tradlo.example</span></li>
        <li><svg width="9" height="9" viewBox="0 0 9 9"><path d="M1 0h2l1 2-1 1c.5 1.2 1.8 2.5 3 3l1-1 2 1v2c-4 .5-8.5-4-8-8z" fill="#fff"/></svg><span>000.000.000</span></li>
      </ul>
      <div class="socials"><span></span><span></span><span></span><span></span></div>
    </div>
  </div>
  <div class="copyright"><span>© Copyright 2017 TRADLO. All Right Reserved</span></div>
</footer>

</div>
</body>
</html>
```